The Harlow Law Firm, PC

Dwight K. Harlow
Attorney at Law
physical address: 735 E. 22nd Avenue
Greenville, NC 27911

mailing: P.O. Box 5870
Greenville, NC 27913

o. 555.013.4471
f. 555.013.8625

www.harlowlegal-ex.com

Industry/Entity Type

Attorney

Contact Information for Business Card

Attorney name
Office Phone number
Office Fax number
Mailing address and physical address
website address

Requirements
Must have
• Clean fresh design - I hate the website

```html
<!DOCTYPE html>
<html lang="en">
<head>
<meta charset="utf-8">
<title>The Harlow Law Firm, PC — Stationery</title>
<link rel="stylesheet" href="https://fonts.googleapis.com/css2?family=Oswald:wght@500;600&family=Arimo:wght@400&display=swap">
<style>
  :root {
    --brown: #4a4032;
    --ink: #000000;
    --paper: #ffffff;
    --card-text: #ffffff;
    --ghost: #f4f3f1;
    --heading: "Oswald", "Arial Narrow", sans-serif;
    --body: "Arimo", Arial, sans-serif;
  }
  * { box-sizing: border-box; margin: 0; padding: 0; }
  html, body { width: 1200px; height: 703px; overflow: hidden; background: var(--paper); }
  .sheet {
    position: relative; width: 1200px; height: 703px;
    border: 1px solid var(--ink); font-family: var(--body); color: var(--brown);
  }

  /* Letterhead */
  .letterhead {
    position: absolute; left: 10px; top: 9px; width: 529px; height: 686px;
    border: 2px solid var(--ink); background: var(--paper); overflow: hidden;
  }
  .letterhead .wordmark {
    position: absolute; left: 28px; top: 28px; width: 200px;
    font-family: var(--heading); font-weight: 600; font-size: 22px; line-height: 1.05;
    color: var(--brown);
  }
  .letterhead .site {
    position: absolute; left: 28px; top: 119px;
    font-family: var(--heading); font-weight: 600; font-size: 10px; color: var(--brown);
  }
  .letterhead .contact {
    position: absolute; right: 29px; top: 28px; text-align: right;
    font-size: 9px; line-height: 12px; color: var(--brown);
  }
  .contact .label { font-family: var(--heading); font-weight: 600; font-size: 11px; line-height: 14px; }
  .contact .phones { font-family: var(--heading); font-weight: 600; font-size: 10px; letter-spacing: 0.5px; line-height: 12px; margin-top: 3px; }
  .letterhead .rule {
    position: absolute; left: 28px; top: 135px; width: 468px; height: 3px; background: var(--brown);
  }
  .letterhead .ghost-mark {
    position: absolute; left: 58px; top: 235px;
    font-family: var(--heading); font-weight: 600; font-size: 86px; line-height: 1.05;
    color: var(--ghost); letter-spacing: 2px;
  }

  /* Labels */
  .side-label { position: absolute; font-family: var(--body); font-size: 19px; color: var(--ink); }
  .side-label.front { left: 656px; top: 113px; }
  .side-label.back { left: 986px; top: 302px; }

  /* Business cards */
  .card {
    position: absolute; width: 321px; height: 184px; background: var(--brown); color: var(--card-text);
  }
  .card.front-a { left: 547px; top: 147px; }
  .card.front-b { left: 547px; top: 334px; height: 182px; }
  .card.front-c { left: 547px; top: 520px; height: 182px; }
  .card.back { left: 873px; top: 333px; width: 321px; height: 184px; }

  .card .el { position: absolute; }
  .card .mini-mark {
    font-family: var(--heading); font-weight: 600; font-size: 11px; line-height: 12px; width: 90px;
  }
  .card .name {
    font-family: var(--heading); font-weight: 600; font-size: 16px; letter-spacing: 2px; line-height: 18px;
  }
  .card .title { font-size: 12px; line-height: 14px; }
  .card .phones {
    font-family: var(--heading); font-weight: 600; font-size: 12px; letter-spacing: 1px; line-height: 15px;
  }
  .card .site { font-family: var(--heading); font-weight: 600; font-size: 13px; }
  .card .address { font-size: 12px; line-height: 14px; }

  .card.back .back-mark {
    position: absolute; left: 0; right: 0; top: 42px; text-align: center;
    font-family: var(--heading); font-weight: 600; font-size: 26px; line-height: 1.1;
  }
  .card.back .site { left: 0; right: 0; top: 132px; text-align: center; font-size: 12px; }
</style>
</head>
<body>
<main class="sheet">

  <section class="letterhead" aria-label="Letterhead">
    <div class="wordmark">The Harlow<br>Law Firm, PC</div>
    <div class="site">www.harlowlegal-ex.com</div>
    <div class="contact">
      <div class="label">Office Address:</div>
      <div>735 E. 22nd Avenue</div>
      <div>Greenville, NC 27911</div>
      <div class="label">Mailing Address:</div>
      <div>P.O. Box 5870</div>
      <div>Greenville, NC 27913</div>
      <div class="phones">o. 555.013.4471<br>f. 555.013.8625</div>
    </div>
    <div class="rule"></div>
    <div class="ghost-mark" aria-hidden="true">The<br>Harlow<br>Law Firm, PC</div>
  </section>

  <div class="side-label front">Front Side</div>
  <div class="side-label back">Back Side</div>

  <article class="card front-a" aria-label="Business card front, option A">
    <div class="el mini-mark" style="left:17px;top:22px;">The Harlow<br>Law Firm, PC</div>
    <div class="el site" style="left:140px;top:40px;">www.harlowlegal-ex.com</div>
    <div class="el name" style="left:17px;top:64px;">Dwight K. Harlow</div>
    <div class="el title" style="left:18px;top:84px;">Attorney at Law</div>
    <div class="el phones" style="left:198px;top:66px;">o. 555.013.4471<br>f. 555.013.8625</div>
    <div class="el address" style="left:17px;top:107px;">Mailing Address: P.O. Box 5870<br>Greenville, NC 27913</div>
    <div class="el address" style="left:17px;top:142px;">Office Address: 735 E. 22nd Avenue<br>Greenville, NC 27911</div>
  </article>

  <article class="card front-b" aria-label="Business card front, option B">
    <div class="el name" style="left:17px;top:14px;">Dwight K. Harlow</div>
    <div class="el title" style="left:18px;top:34px;">Attorney at Law</div>
    <div class="el phones" style="left:198px;top:16px;">o. 555.013.4471<br>f. 555.013.8625</div>
    <div class="el mini-mark" style="left:17px;top:58px;">The Harlow<br>Law Firm, PC</div>
    <div class="el site" style="left:140px;top:77px;">www.harlowlegal-ex.com</div>
    <div class="el address" style="left:17px;top:106px;">Mailing Address: P.O. Box 5870<br>Greenville, NC 27913</div>
    <div class="el address" style="left:17px;top:141px;">Office Address: 735 E. 22nd Avenue<br>Greenville, NC 27911</div>
  </article>

  <article class="card front-c" aria-label="Business card front, option C">
    <div class="el name" style="left:17px;top:14px;">Dwight K. Harlow</div>
    <div class="el title" style="left:18px;top:34px;">Attorney at Law</div>
    <div class="el phones" style="left:198px;top:16px;">o. 555.013.4471<br>f. 555.013.8625</div>
    <div class="el site" style="left:17px;top:82px;">www.harlowlegal-ex.com</div>
    <div class="el address" style="left:17px;top:106px;">Mailing Address: P.O. Box 5870<br>Greenville, NC 27913</div>
    <div class="el address" style="left:17px;top:141px;">Office Address: 735 E. 22nd Avenue<br>Greenville, NC 27911</div>
  </article>

  <article class="card back" aria-label="Business card back">
    <div class="back-mark">The Harlow<br>Law Firm, PC</div>
    <div class="el site">www.harlowlegal-ex.com</div>
  </article>

</main>
</body>
</html>
```